Beautiful design for wordpress

I need a beautiful, colourful and feminine website. My business is called 'The Velvet Lantern', and I sell crystals, books, CD's, pendulums and other metaphysical items. I also provide Reiki (energy healing).
I want this design to be eye catching and inspire happiness and joy in those who see it. And I would love to see the use of the logo and its colours :)
Please add these on the web design: Home, About, Online store, Blog

Industry/Entity Type

Business

Requirements
Must have
• Colourful and playful, must use the logo somewhere, have the words on a menu saying 'Home, Blog, Online store and about' (or similar to those)And the design must stand out!
Should not have
• grey, brown and other boring colours.

```html
<!DOCTYPE html>
<html lang="en">
<head>
<meta charset="utf-8">
<title>The Velvet Lantern</title>
<link rel="stylesheet" href="https://fonts.googleapis.com/css2?family=Yellowtail&display=swap">
<style>
  :root {
    --sky: #00a8d6;
    --white: #ffffff;
    --ink: #77726d;
  }
  html, body {
    margin: 0;
    padding: 0;
    overflow: hidden;
  }
  .page {
    position: relative;
    width: 1200px;
    height: 873px;
    background: var(--sky);
    overflow: hidden;
    font-family: "Yellowtail", cursive;
  }
  .main-nav {
    position: absolute;
    inset: 0;
  }
  .nav-item {
    position: absolute;
    top: 56px;
    width: 180px;
    margin-left: -90px;
    display: flex;
    flex-direction: column;
    align-items: center;
    text-decoration: none;
    color: var(--white);
  }
  .nav-label {
    font-size: 50px;
    line-height: 60px;
    height: 66px;
  }
  .nav-icon {
    width: 106px;
    height: 106px;
    border-radius: 50%;
    background: var(--white);
    display: flex;
    align-items: center;
    justify-content: center;
  }
  .nav-icon svg {
    width: 60px;
    height: 60px;
  }
  .nav-home  { left: 320px; }
  .nav-about { left: 520px; }
  .nav-store { left: 721px; }
  .nav-blog  { left: 922px; }

  .brand-badge {
    position: absolute;
    left: 355px;
    top: 282px;
    width: 472px;
    height: 472px;
    border-radius: 50%;
    background: var(--white);
    display: flex;
    align-items: center;
    justify-content: center;
  }
  .brand-name {
    margin: 0;
    font-family: "Yellowtail", cursive;
    font-weight: 400;
    font-size: 72px;
    line-height: 1.05;
    color: var(--ink);
    text-align: center;
  }
</style>
</head>
<body>
<div class="page">
  <nav class="main-nav">
    <a class="nav-item nav-home" href="#">
      <span class="nav-label">Home</span>
      <span class="nav-icon">
        <svg viewBox="0 0 60 60" aria-hidden="true">
          <path d="M30 6 C14 6 8 16 8 24 L18 24 L14 54 L24 54 C24 46 26 42 30 42 C34 42 36 46 36 54 L46 54 L42 24 L52 24 C52 16 46 6 30 6 Z" fill="var(--sky)"/>
          <circle cx="30" cy="18" r="5" fill="var(--white)"/>
          <path d="M30 13 V23 M25 18 H35" stroke="var(--sky)" stroke-width="1.5"/>
        </svg>
      </span>
    </a>
    <a class="nav-item nav-about" href="#">
      <span class="nav-label">About</span>
      <span class="nav-icon">
        <svg viewBox="0 0 60 60" aria-hidden="true">
          <path d="M22 20 C22 12 38 10 38 20 C38 28 30 28 30 38" fill="none" stroke="var(--sky)" stroke-width="4" stroke-linecap="round"/>
          <circle cx="30" cy="47" r="3.5" fill="var(--sky)"/>
        </svg>
      </span>
    </a>
    <a class="nav-item nav-store" href="#">
      <span class="nav-label">Store</span>
      <span class="nav-icon">
        <svg viewBox="0 0 60 60" aria-hidden="true">
          <path d="M12 28 C12 10 48 10 48 28" fill="none" stroke="var(--sky)" stroke-width="5"/>
          <rect x="4" y="26" width="52" height="26" rx="6" fill="var(--sky)"/>
          <g fill="var(--white)">
            <rect x="15" y="32" width="5" height="5"/><rect x="23" y="32" width="5" height="5"/>
            <rect x="31" y="32" width="5" height="5"/><rect x="39" y="32" width="5" height="5"/>
            <rect x="15" y="41" width="5" height="5"/><rect x="23" y="41" width="5" height="5"/>
            <rect x="31" y="41" width="5" height="5"/><rect x="39" y="41" width="5" height="5"/>
          </g>
        </svg>
      </span>
    </a>
    <a class="nav-item nav-blog" href="#">
      <span class="nav-label">Blog</span>
      <span class="nav-icon">
        <svg viewBox="0 0 60 60" aria-hidden="true">
          <path d="M32 10 C46 10 56 18 56 28 C56 38 46 46 32 46 C26 46 20 44 16 42 L6 50 L10 38 C7 35 6 32 6 28 C6 18 18 10 32 10 Z" fill="var(--sky)"/>
        </svg>
      </span>
    </a>
  </nav>

  <div class="brand-badge">
    <h1 class="brand-name">The Velvet<br>Lantern</h1>
  </div>
</div>
</body>
</html>
```